Create a Stalvik-looking dashboard for our Open Compass Speedometer that can look similar to my AI-generated dashboard attached, but with: 1) clear borders on all four sides, 2) is created in a way that we can modify the numbers weekly, say maybe you create the graphic that we can inset the excel spreadsheet numbers into, but ideally mixed with the Stalvik look black leather bubble design shown in the dashboard?; 3) uses the exact numbers shown in the attachment; 4) the speedometer on top should have four equal colors of red on left (-1), then yellow (0), then light green (1), then medium green (2); 5) the gauge on the top left should be the graphic that includes 0-100% bar that is currently 33%, and right below that a -20 to +20 bar with the arrow pointing to 11.9%, with color coding similar to the graphic; 6) replace the Stalvik logo in the middle with a similar shaped shield with blue background with the "T" logo with the eagle inside it, like attached

```html
<!DOCTYPE html>
<html lang="en">
<head>
<meta charset="utf-8">
<title>Open Compass Speedometer</title>
<link rel="stylesheet" href="https://fonts.googleapis.com/css2?family=Exo+2:wght@600;700;800&display=swap">
<style>
  :root {
    --bg: #2b2b2b;
    --housing: #121212;
    --housing-edge: #4a4a4a;
    --leather-red: #c8161b;
    --gold: #f0b43c;
    --text-light: #e8e8e8;
    --header-text: #c9cfd2;
    --row-bull: #2fe23f;
    --row-bullish: #22d466;
    --row-bearish: #cdb21c;
    --row-bear: #e2303a;
    --cell-text: #111;
    --gauge-red: #d42020;
    --gauge-yellow: #e0b21c;
    --gauge-lightgreen: #7cc63a;
    --gauge-green: #1f8f2c;
    --badge-blue: #1c3f8c;
  }
  * { margin: 0; padding: 0; box-sizing: border-box; }
  html, body { width: 1200px; height: 800px; overflow: hidden; background: var(--bg); }
  body { font-family: "Exo 2", sans-serif; }
  .dashboard { position: relative; width: 1200px; height: 800px; }
  .dashboard-art { position: absolute; inset: 0; }
  .gauge-label { font-family: "Exo 2", sans-serif; font-weight: 700; }
  .dashboard-title {
    position: absolute; left: 0; width: 1200px; top: 400px;
    text-align: center; color: var(--gold); font-size: 25px; font-weight: 800;
    letter-spacing: 0.5px; text-shadow: 0 2px 3px #000;
  }
  .trend-header {
    position: absolute; top: 454px; left: 192px; width: 824px;
    display: grid; grid-template-columns: 316px 216px 1fr;
    color: var(--header-text); font-size: 16px; font-weight: 700; text-align: center;
  }
  .trend-table {
    position: absolute; left: 192px; top: 492px; width: 824px; height: 178px;
    clip-path: polygon(0 0, 100% 0, 94.2% 100%, 4.9% 100%);
    border-radius: 0 0 12px 12px;
    display: grid; grid-template-rows: repeat(4, 1fr);
  }
  .trend-row {
    display: grid; grid-template-columns: 316px 216px 1fr;
    border-bottom: 2px solid #0c0c0c;
    font-size: 16px; font-weight: 700; color: var(--cell-text);
  }
  .trend-row:last-child { border-bottom: 0; }
  .trend-row > div { display: flex; align-items: center; justify-content: center; }
  .trend-row > div + div { border-left: 2px solid #0c0c0c; }
  .trend-row .gear { justify-content: flex-start; padding-left: 72px; }
  .row-bull { background: var(--row-bull); }
  .row-bullish { background: var(--row-bullish); }
  .row-bearish { background: var(--row-bearish); }
  .row-bear { background: var(--row-bear); }
</style>
</head>
<body>
<div class="dashboard">
  <svg class="dashboard-art" width="1200" height="800" viewBox="0 0 1200 800">
    <defs>
      <linearGradient id="left-gauge-band" x1="0" x2="1">
        <stop offset="0" stop-color="var(--gauge-red)"/>
        <stop offset="0.5" stop-color="var(--gauge-yellow)"/>
        <stop offset="1" stop-color="var(--gauge-green)"/>
      </linearGradient>
      <linearGradient id="right-gauge-band" x1="0" x2="1">
        <stop offset="0" stop-color="var(--gauge-green)"/>
        <stop offset="0.5" stop-color="var(--gauge-yellow)"/>
        <stop offset="1" stop-color="var(--gauge-red)"/>
      </linearGradient>
      <radialGradient id="hub-gold" cx="0.4" cy="0.35">
        <stop offset="0" stop-color="#ffe9a0"/>
        <stop offset="1" stop-color="#b07a14"/>
      </radialGradient>
    </defs>

    <!-- housing body -->
    <path class="housing" d="M60,470 L62,340 Q72,250 200,215 L380,180 Q420,102 608,98 Q796,102 836,180 L1010,215 Q1128,240 1140,340 L1150,470 Z"
          fill="var(--housing)" stroke="var(--housing-edge)" stroke-width="4"/>
    <!-- red leather wings -->
    <path class="leather-wing" d="M64,300 Q82,218 230,182 L384,152 L394,188 L232,214 Q108,240 80,306 Z" fill="var(--leather-red)"/>
    <path class="leather-wing" d="M1136,300 Q1118,218 970,182 L816,152 L806,188 L968,214 Q1092,240 1120,306 Z" fill="var(--leather-red)"/>

    <!-- left gauge -->
    <g class="gauge-percent">
      <circle cx="246" cy="382" r="104" fill="#0a0a0a" stroke="#555" stroke-width="4"/>
      <circle cx="246" cy="382" r="92" fill="none" stroke="#3a3a3a" stroke-width="6" stroke-dasharray="1 3"/>
      <path d="M184,382 A62,62 0 0 1 308,382" fill="none" stroke="url(#left-gauge-band)" stroke-width="44"/>
      <circle cx="246" cy="382" r="48" fill="#0b0b0b" stroke="#6a6a6a" stroke-width="3"/>
      <polygon points="218,310 224,314 232,336" fill="var(--gold)"/>
      <text class="gauge-label" x="246" y="391" text-anchor="middle" font-size="22" fill="var(--text-light)">33%</text>
    </g>

    <!-- right gauge -->
    <g class="gauge-change">
      <circle cx="964" cy="384" r="104" fill="#0a0a0a" stroke="#555" stroke-width="4"/>
      <circle cx="964" cy="384" r="92" fill="none" stroke="#3a3a3a" stroke-width="6" stroke-dasharray="1 3"/>
      <path d="M902,384 A62,62 0 0 1 1026,384" fill="none" stroke="url(#right-gauge-band)" stroke-width="44"/>
      <circle cx="964" cy="384" r="48" fill="#0b0b0b" stroke="#6a6a6a" stroke-width="3"/>
      <polygon points="967,308 963,334 971,334" fill="var(--gold)"/>
      <g class="gauge-label" font-size="10" fill="var(--gold)" text-anchor="middle">
        <text x="924" y="327">10</text>
        <text x="978" y="310">0</text>
        <text x="1024" y="347">-10</text>
        <text x="894" y="376">20</text>
        <text x="1023" y="417">-20</text>
      </g>
      <text class="gauge-label" x="964" y="393" text-anchor="middle" font-size="22" fill="var(--text-light)">11.9%</text>
    </g>

    <!-- center speedometer -->
    <g class="gauge-speed">
      <circle cx="608" cy="352" r="186" fill="#0a0a0a" stroke="#5a5a5a" stroke-width="5"/>
      <circle cx="608" cy="352" r="170" fill="none" stroke="#444" stroke-width="14" stroke-dasharray="1 4"/>
      <path d="M498,352 A110,110 0 0 1 530.2,274.2" fill="none" stroke="var(--gauge-red)" stroke-width="80"/>
      <path d="M530.2,274.2 A110,110 0 0 1 608,242" fill="none" stroke="var(--gauge-yellow)" stroke-width="80"/>
      <path d="M608,242 A110,110 0 0 1 685.8,274.2" fill="none" stroke="var(--gauge-lightgreen)" stroke-width="80"/>
      <path d="M685.8,274.2 A110,110 0 0 1 718,352" fill="none" stroke="var(--gauge-green)" stroke-width="80"/>
      <circle cx="608" cy="352" r="68" fill="#0b0b0b" stroke="#333" stroke-width="4"/>
      <g class="gauge-label" font-size="28" fill="var(--gold)" text-anchor="middle">
        <text x="446" y="327">-1</text>
        <text x="525" y="236">0</text>
        <text x="690" y="236">1</text>
        <text x="766" y="327">2</text>
      </g>
      <g class="brand-mark">
        <circle cx="608" cy="232" r="12" fill="var(--badge-blue)"/>
        <text x="608" y="262" text-anchor="middle" font-family="Exo 2, sans-serif" font-weight="700" font-size="12" fill="var(--gold)">OPEN COMPASS</text>
      </g>
      <polygon points="707,253 602,346 614,358" fill="var(--gold)"/>
      <circle cx="608" cy="352" r="15" fill="url(#hub-gold)"/>
    </g>

    <!-- lower panel and table tray -->
    <path class="lower-panel" d="M45,482 Q42,466 62,465 L360,458 Q400,388 608,386 Q816,388 856,458 L1146,465 Q1164,468 1158,486 L1094,500 Q1042,506 1032,540 L1012,682 Q1002,706 976,706 L238,706 Q212,706 204,682 L186,540 Q178,506 128,500 Z"
          fill="var(--housing)" stroke="var(--housing-edge)" stroke-width="4"/>
    <path d="M360,458 Q400,388 608,386 Q816,388 856,458" fill="none" stroke="#666" stroke-width="2"/>
  </svg>

  <div class="dashboard-title">OPEN COMPASS SPEEDOMETER</div>

  <div class="trend-header">
    <div>GEAR</div>
    <div>CURRENT TREND</div>
    <div>LAST TREND CHANGE</div>
  </div>

  <div class="trend-table">
    <div class="trend-row row-bull">
      <div class="gear">2 TURBO BOOST</div><div>BULL</div><div>FRIDAY, AUGUST 15, 2025</div>
    </div>
    <div class="trend-row row-bullish">
      <div class="gear">1 ACCELERATOR PEDAL</div><div>BULISH</div><div>-</div>
    </div>
    <div class="trend-row row-bearish">
      <div class="gear">0 BRAKES</div><div>BEARISH</div><div>-</div>
    </div>
    <div class="trend-row row-bear">
      <div class="gear">-1 REVERSE</div><div>BEAR</div><div>-</div>
    </div>
  </div>
</div>
</body>
</html>
```